Business card design for my company.
I would like the card's background colour to be black. You can also see our web site to get an idea of our brand. https://www.tmwhomecrafting.com.au/
- Name
- Email

```html
<!DOCTYPE html>
<html lang="en">
<head>
<meta charset="utf-8">
<title>TMW Home Crafting – Business Card</title>
<link href="https://fonts.googleapis.com/css2?family=Open+Sans:wght@400;600;700&family=Roboto:wght@400&display=swap" rel="stylesheet">
<style>
  :root {
    --stage: #2a2a2a;
    --card-black: #1f1f20;
    --card-white: #f7f7f5;
    --brand-green: #17953f;
    --ink: #141414;
    --muted-grey: #c9c9c9;
    --logo-grey: #4a4a4c;
  }
  * { margin: 0; padding: 0; box-sizing: border-box; }
  html, body { width: 1200px; height: 852px; overflow: hidden; }
  body {
    background: var(--stage);
    font-family: "Open Sans", Arial, sans-serif;
    position: relative;
  }
  .card {
    position: absolute;
    top: 283px;
    width: 500px;
    height: 286px;
    border-radius: 22px;
    overflow: hidden;
  }
  /* Back side */
  .card--back {
    left: 70px;
    background: var(--card-black);
    border-bottom: 7px solid var(--brand-green);
  }
  .card--back .brand-name {
    position: absolute;
    top: 108px;
    left: 0;
    width: 100%;
    text-align: center;
    font-weight: 700;
    font-size: 34px;
    letter-spacing: 2px;
    color: var(--logo-grey);
    text-transform: uppercase;
  }
  .card--back .website {
    position: absolute;
    bottom: 22px;
    left: 0;
    width: 100%;
    text-align: center;
    font-family: "Roboto", Arial, sans-serif;
    font-size: 13px;
    color: var(--muted-grey);
  }
  /* Front side */
  .card--front {
    left: 630px;
    background: var(--card-white);
  }
  .card--front .brand-name {
    position: absolute;
    top: 40px;
    left: 34px;
    font-weight: 700;
    font-size: 30px;
    letter-spacing: 1.5px;
    color: var(--ink);
    text-transform: uppercase;
    display: flex;
    align-items: center;
    gap: 12px;
  }
  .brand-mark-square {
    width: 22px;
    height: 22px;
    background: var(--brand-green);
  }
  .contact-list {
    position: absolute;
    top: 112px;
    left: 286px;
    list-style: none;
    font-family: "Roboto", Arial, sans-serif;
    font-size: 12.5px;
    color: var(--ink);
  }
  .contact-list li {
    display: flex;
    align-items: center;
    gap: 8px;
    height: 19px;
  }
  .contact-list svg { width: 11px; height: 11px; fill: var(--brand-green); flex: none; }
  .person {
    position: absolute;
    left: 34px;
    bottom: 40px;
  }
  .person__name {
    font-weight: 600;
    font-size: 20px;
    color: var(--brand-green);
    line-height: 1.1;
  }
  .person__role {
    font-size: 13px;
    color: var(--ink);
  }
  .base-band {
    position: absolute;
    left: 0; bottom: 0;
    width: 100%;
    height: 10px;
    background: var(--ink);
  }
  .company-tab {
    position: absolute;
    right: 0;
    bottom: 0;
    width: 200px;
    height: 62px;
    background: var(--brand-green);
    border-top-left-radius: 16px;
    color: #fff;
    font-family: "Roboto", Arial, sans-serif;
    font-size: 13px;
    padding: 10px 0 0 24px;
  }
</style>
</head>
<body>
  <section class="card card--back" aria-label="Card back">
    <div class="brand-name">TMW Home Crafting</div>
    <div class="website">www.tmwhomecrafting.com.au</div>
  </section>

  <section class="card card--front" aria-label="Card front">
    <div class="brand-name"><span class="brand-mark-square"></span>TMW Home Crafting</div>

    <ul class="contact-list">
      <li><svg viewBox="0 0 24 24"><path d="M6.6 10.8a15 15 0 0 0 6.6 6.6l2.2-2.2a1 1 0 0 1 1-.25 11.4 11.4 0 0 0 3.6.6 1 1 0 0 1 1 1V20a1 1 0 0 1-1 1A17 17 0 0 1 3 4a1 1 0 0 1 1-1h3.5a1 1 0 0 1 1 1c0 1.25.2 2.45.6 3.6a1 1 0 0 1-.25 1z"/></svg>0400 123 456</li>
      <li><svg viewBox="0 0 24 24"><path d="M2 5h20v14H2z M2 5l10 8 10-8" /></svg>info@tmwhomecrafting.com.au</li>
      <li><svg viewBox="0 0 24 24"><circle cx="12" cy="12" r="10"/></svg>www.tmwhomecrafting.com.au</li>
      <li><svg viewBox="0 0 24 24"><path d="M12 2a7 7 0 0 0-7 7c0 5 7 13 7 13s7-8 7-13a7 7 0 0 0-7-7zm0 9.5A2.5 2.5 0 1 1 12 6.5a2.5 2.5 0 0 1 0 5z"/></svg>Northfield, Tasmania, Australia</li>
    </ul>

    <div class="person">
      <div class="person__name">Liam Harper</div>
      <div class="person__role">General Manager</div>
    </div>

    <div class="base-band"></div>
    <div class="company-tab">TMW Home Crafting</div>
  </section>
</body>
</html>
```